Hardcore nerd needs to stand out in a sea of dull Defence business cards

Wombarra Devices is a new Australian consulting engineering company that turns research and theory into practical systems. No evangelistic fluff, just mathematics and physics into electronic and optical circuits for consumer products, scientific research or Defence applications.

We already have a recognised logo (provided) which is often dark blue/black on a light background but we're open to other combinations. (Us engineers tend to have limited aesthetic imagination :)

Some of our recent products have included:
* Instrumentation for electrical testing,
* Radar jammers,
* GPS antenna design,
* Satellite tracking systems,
* High power lasers

We're open to both single and double-sided designs - happy to be convinced either way.

P.S. Another group is working on the web page, so - alas - our web site is currently of no use for images/ideas...

Target Market(s)

Engineering managers,
Scientists

Contact Information for Business Card

Dr Colin Harte
R&D Engineer

colin@wombarradevices.com.au
0427 563 710

PO Box XXX (to be confirmed)
Kelsby ACT 2917
Australia

Font styles to use
Serif
Sans Serif

Colors

Designer to choose colors to be used in the design.

Requirements
Must have
• My contact details!
• I've had many (great) "bold and plain" designs submitted already, so feel free to be artistically creative :)
• Happy to take advice re fonts/colours/printability etc.
Nice to have
• I'm not sure if "lists" are more at home on a CV than a business card, but representative services include:
• Applied electromagnetics
• RF and high speed electronics
• Signal and image processing
• Electro-optical and laser systems
• Concept-to-prototype design services
• If you're considering double sided cards, then often measuring/alignment grids/rulers feature on the back of similar cards.
• e.g. https://www.veltranoptics.example/newgrouppage9.cfm?objectgroup_id=4183
• https://www.veltranoptics.example/newgrouppage9.cfm?objectgroup_ID=4185
• ..or even a "Smith chart" (google will return lots)
• Generic images to represent a capability might work - googling images associated with keyword for each of these areas might help:
• - "passive radar", "phased array", "fdtd", "vircator"
• RF and high speed electronic design
• - "smith chart", "microstrip circuits", "dimensioned drawing", "electronic schematic"
• - "dft", "iir filter"
• - "optical cavity". "laser energy level diagram"
• Background/watermarked images outlines/wireframes/schematics would probably look OK.
Should not have
• If a list of projects/services is provided, it is important not to make the client feel that this is "all" the company can do. Engineering design is a creative discipline (like graphics :)
• Please, no stock "military" snaps like planes, missiles, etc!

```html
<!DOCTYPE html>
<html lang="en">
<head>
<meta charset="utf-8">
<title>Wombarra Devices — Business Card</title>
<link rel="stylesheet" href="https://fonts.googleapis.com/css2?family=Lato:wght@400;700;900&family=Arimo:wght@700&display=swap">
<style>
  :root {
    --navy: #0b2a6f;
    --ink: #1f1f1f;
    --rule: #9a9a9a;
    --paper: #ffffff;
    --paper-soft: #f7f7f7;
    --backdrop: #2a2a2c;
  }
  * { box-sizing: border-box; margin: 0; padding: 0; }
  html, body {
    width: 1200px; height: 900px; overflow: hidden;
    background: var(--backdrop);
    font-family: "Lato", Arial, sans-serif;
  }
  .stage {
    width: 1200px; height: 900px;
    display: flex; align-items: center; justify-content: center; gap: 40px;
  }
  .card {
    position: relative;
    width: 540px; height: 310px;
    background: var(--paper);
    border-bottom: 9px solid var(--navy);
  }
  .card--front { background: var(--paper-soft); }

  /* Front */
  .brand {
    position: absolute; left: 70px; top: 70px;
    display: flex; align-items: center; gap: 18px;
  }
  .brand__dot {
    width: 74px; height: 74px; border-radius: 50%;
    background: var(--navy);
  }
  .brand__name {
    font-family: "Lato", Arial, sans-serif;
    font-weight: 900; font-size: 40px; line-height: 1;
    letter-spacing: 1px; color: var(--navy); text-transform: uppercase;
  }
  .services {
    position: absolute; left: 40px; right: 30px; top: 205px;
    display: grid; grid-template-columns: 1fr 1fr; gap: 4px 20px;
    list-style: none;
    font-size: 16px; color: #3a3a3a;
  }
  .services li::before {
    content: "•"; color: var(--navy); margin-right: 5px;
  }

  /* Back */
  .contact {
    position: absolute; left: 0; right: 0; top: 42px;
    text-align: center; color: var(--ink);
  }
  .contact__name {
    font-family: "Arimo", Arial, sans-serif; font-weight: 700;
    font-size: 20px; color: var(--navy); letter-spacing: .3px;
  }
  .contact__role { font-size: 14px; color: #444; margin-top: 2px; }
  .contact__rule {
    width: 170px; height: 1px; background: var(--rule);
    margin: 8px auto;
  }
  .contact__icons { display: flex; justify-content: center; gap: 5px; margin: -4px 0 4px; }
  .contact__icons svg { width: 20px; height: 20px; }
  .contact__line { font-size: 15px; line-height: 1.3; }
</style>
</head>
<body>
<main class="stage">

  <section class="card card--front" aria-label="Card front">
    <div class="brand">
      <span class="brand__dot"></span>
      <span class="brand__name">Wombarra<br>Devices</span>
    </div>
    <ul class="services">
      <li>Applied electromagnetics</li>
      <li>RF and high speed electronics</li>
      <li>Signal and image processing</li>
      <li>Electro-optical and laser systems</li>
    </ul>
  </section>

  <section class="card card--back" aria-label="Card back">
    <div class="contact">
      <h1 class="contact__name">DR COLIN HARTE</h1>
      <p class="contact__role">R&amp;D Engineer</p>
      <div class="contact__rule"></div>
      <div class="contact__icons">
        <svg viewBox="0 0 20 20" aria-label="Phone"><circle cx="10" cy="10" r="10" fill="var(--navy)"/><path d="M6 7c1-2 2-2 2-1l1 2-1 1c1 1 2 2 3 2l1-1 2 1c1 0 0 1-1 2-3 1-8-3-7-6z" fill="#fff"/></svg>
        <svg viewBox="0 0 20 20" aria-label="Email"><circle cx="10" cy="10" r="10" fill="var(--navy)"/><rect x="5" y="6.5" width="10" height="7" fill="#fff"/><path d="M5 6.5l5 4 5-4" fill="none" stroke="var(--navy)" stroke-width="1"/></svg>
        <svg viewBox="0 0 20 20" aria-label="Web"><circle cx="10" cy="10" r="10" fill="var(--navy)"/><circle cx="10" cy="10" r="5" fill="none" stroke="#fff" stroke-width="1.3"/><path d="M5 10h10M10 5c-2 3-2 7 0 10M10 5c2 3 2 7 0 10" fill="none" stroke="#fff" stroke-width="1"/></svg>
      </div>
      <p class="contact__line">0427 563 710</p>
      <p class="contact__line">colin@wombarradevices.com.au</p>
      <p class="contact__line">www.wombarradevices.com.au</p>
      <div class="contact__rule"></div>
      <p class="contact__line">PO Box XXX</p>
      <p class="contact__line">Kelsby ACT 2917, Australia</p>
    </div>
  </section>

</main>
</body>
</html>
```